Business card por a urban DJ, up scale audience target

Need a sober design, modern, conservative colors but i can consider some options, y play rnb, hip hop, EDM and top40.

Business card for contact and personal info, double sided, use logo attrached please; im 42 so i need a card acording to my age an target audience.

Target Market(s)

Adult people, up scale audience

Industry/Entity Type

Music Download

Contact Information for Business Card

Cel (318) 4207265518 www.lumadrift.com

Requirements
Must have
• open mind
Nice to have
• open mind
Should not have
• DJ

```html
<!DOCTYPE html>
<html lang="en">
<head>
<meta charset="utf-8">
<title>Luma – Business Card</title>
<link rel="stylesheet" href="https://fonts.googleapis.com/css2?family=Exo+2:wght@500;700&display=swap">
<style>
  :root {
    --backdrop: #2f3d44;
    --ink: #3b393a;
    --band-dark: #3a3839;
    --band-grey: #8b8a8b;
    --paper: #ffffff;
  }
  * { box-sizing: border-box; margin: 0; padding: 0; }
  html, body {
    width: 1200px; height: 900px; overflow: hidden;
    background: var(--backdrop);
    font-family: "Exo 2", sans-serif;
    color: var(--ink);
  }
  .sheet {
    width: 1200px; height: 900px;
    display: flex; flex-direction: column;
    align-items: center; justify-content: center; gap: 40px;
  }
  .card {
    position: relative;
    width: 660px; height: 377px;
    background: var(--paper);
    overflow: hidden;
    box-shadow: 0 10px 30px rgba(0,0,0,.35);
  }
  .card__shapes { position: absolute; inset: 0; width: 100%; height: 100%; }

  /* Front side */
  .front__content {
    position: absolute; left: 48px; top: 40px; width: 380px;
    display: flex; flex-direction: column; align-items: center;
  }
  .brand-name {
    font-weight: 700; font-size: 78px; line-height: 1;
    letter-spacing: 6px; color: var(--ink);
  }
  .brand-rule {
    width: 300px; height: 3px; background: var(--ink); margin-top: 10px;
  }
  .genres {
    margin-top: 14px; font-weight: 500; font-size: 20px;
    letter-spacing: 3px; word-spacing: 12px;
  }
  .contact-list {
    list-style: none; margin-top: 34px; align-self: flex-start;
    display: flex; flex-direction: column; gap: 16px;
  }
  .contact-list li {
    display: flex; align-items: center; gap: 14px;
    font-weight: 500; font-size: 25px; letter-spacing: 1.5px;
  }
  .contact-list svg { width: 22px; height: 22px; flex: none; }

  /* Back side: name sits in the middle of the white diagonal band */
  .back__name {
    position: absolute; left: 0; right: 0; top: 112px;
    text-align: center;
    font-weight: 700; font-size: 92px; line-height: 1;
    letter-spacing: 8px;
    color: var(--ink);
  }
</style>
</head>
<body>
<main class="sheet">

  <section class="card card--front" aria-label="Card front">
    <svg class="card__shapes" viewBox="0 0 660 377" preserveAspectRatio="none" aria-hidden="true">
      <polygon points="480,0 660,0 660,377 560,377" fill="var(--band-grey)"/>
      <polygon points="500,0 660,0 660,377 580,377" fill="var(--band-dark)"/>
    </svg>
    <div class="front__content">
      <h1 class="brand-name">LUMA</h1>
      <div class="brand-rule"></div>
      <p class="genres">RNB HIPHOP EDM</p>
      <ul class="contact-list">
        <li>
          <svg viewBox="0 0 24 24" aria-hidden="true"><rect x="6" y="1.5" width="12" height="21" rx="2" fill="none" stroke="currentColor" stroke-width="2"/><line x1="10" y1="19" x2="14" y2="19" stroke="currentColor" stroke-width="2"/></svg>
          <span>(318) 4207265518</span>
        </li>
        <li>
          <svg viewBox="0 0 24 24" aria-hidden="true"><circle cx="12" cy="12" r="10" fill="none" stroke="currentColor" stroke-width="2"/><ellipse cx="12" cy="12" rx="4.5" ry="10" fill="none" stroke="currentColor" stroke-width="1.6"/><line x1="2" y1="12" x2="22" y2="12" stroke="currentColor" stroke-width="1.6"/></svg>
          <span>www.lumadrift.com</span>
        </li>
      </ul>
    </div>
  </section>

  <section class="card card--back" aria-label="Card back">
    <svg class="card__shapes" viewBox="0 0 660 377" preserveAspectRatio="none" aria-hidden="true">
      <rect width="660" height="377" fill="var(--band-dark)"/>
      <polygon points="0,95 660,0 660,25 0,120" fill="var(--band-grey)"/>
      <polygon points="0,120 660,25 660,190 0,330" fill="var(--paper)"/>
      <polygon points="0,330 660,190 660,225 0,345" fill="var(--band-grey)"/>
    </svg>
    <p class="back__name">LUMA</p>
  </section>

</main>
</body>
</html>
```